Harrow Grading LLC business card design

Excavation company business cards

Contact Information for Business Card

Harrow Grading LLC cell phone 208-417-6290 office phone 208-319-4856 harrowgradingllc@maplecove.com Driveways, site prep, retaining walls, septic systems, rock delivery

Colors

Designer to choose colors to be used in the design.

```html
<!DOCTYPE html>
<html lang="en">
<head>
<meta charset="utf-8">
<title>Harrow Grading LLC – Business Card</title>
<link href="https://fonts.googleapis.com/css2?family=Montserrat:wght@700;800&family=Roboto:wght@400;500&display=swap" rel="stylesheet">
<style>
  :root {
    --bg: #c9c9c9;
    --paper: #ffffff;
    --orange: #ee6a1f;
    --charcoal: #3a3a3a;
    --ink: #2b2b2b;
    --rule: #8a8a8a;
    --back: #6a6a6a;
    --back-ink: #4a4a4a;
  }
  * { margin: 0; padding: 0; box-sizing: border-box; }
  html, body {
    width: 1200px; height: 788px; overflow: hidden;
    background: var(--bg);
    font-family: "Roboto", Arial, sans-serif;
  }
  .canvas { position: relative; width: 1200px; height: 788px; }

  .card {
    position: absolute;
    width: 540px; height: 309px;
    overflow: hidden;
    box-shadow: 0 6px 18px rgba(0,0,0,0.18);
  }

  /* Front */
  .card-front { left: 50px; top: 70px; background: var(--paper); }
  .front-band {
    position: absolute; left: 0; bottom: 0; width: 100%; height: 12px;
  }
  .wordmark {
    position: absolute; left: 36px; top: 140px; width: 200px;
    display: flex; align-items: center; gap: 10px;
    font-family: "Montserrat", Arial, sans-serif;
    font-weight: 800; font-size: 24px; line-height: 1.05;
    color: var(--orange); text-transform: uppercase;
  }
  .wordmark .mark-square {
    flex: 0 0 14px; width: 14px; height: 14px; background: var(--orange);
  }
  .divider {
    position: absolute; left: 262px; top: 44px; width: 1px; height: 150px;
    background: var(--rule);
  }
  .details { position: absolute; left: 286px; top: 44px; }
  .name {
    font-family: "Montserrat", Arial, sans-serif;
    font-weight: 700; font-size: 21px; color: var(--orange);
    letter-spacing: 0.5px;
  }
  .role { font-size: 14px; color: var(--ink); margin-top: 2px; }
  .contact-list { list-style: none; margin-top: 22px; }
  .contact-list li {
    display: flex; align-items: center; gap: 8px;
    font-size: 12.5px; color: var(--ink); height: 21px;
  }
  .contact-list svg { width: 11px; height: 11px; flex: 0 0 11px; }

  /* Back */
  .card-back { left: 610px; top: 409px; background: var(--back); }
  .back-wordmark {
    position: absolute; inset: 0;
    display: flex; align-items: center; justify-content: center; gap: 14px;
    font-family: "Montserrat", Arial, sans-serif;
    font-weight: 800; font-size: 34px; color: var(--back-ink);
    text-transform: uppercase;
  }
  .back-wordmark .mark-square { width: 20px; height: 20px; background: var(--back-ink); }
</style>
</head>
<body>
<div class="canvas">

  <section class="card card-front" aria-label="Business card front">
    <div class="wordmark"><span class="mark-square"></span><span>Harrow Grading LLC</span></div>
    <div class="divider"></div>

    <div class="details">
      <div class="name">DALE WARNER</div>
      <div class="role">Founder</div>
      <ul class="contact-list">
        <li>
          <svg viewBox="0 0 12 12"><path d="M2.5 1l2 2.2-1 1.3c.7 1.4 1.6 2.3 3 3l1.3-1L10 8.5 8.8 10.6C5 10 2 7 1.4 3.2z" fill="var(--orange)"/></svg>
          208-319-4856
        </li>
        <li>
          <svg viewBox="0 0 12 12"><rect x="3" y="0.8" width="6" height="10.4" rx="1" fill="none" stroke="var(--orange)" stroke-width="1.4"/></svg>
          208-417-6290
        </li>
        <li>
          <svg viewBox="0 0 12 12"><rect x="0.5" y="2" width="11" height="8" fill="var(--orange)"/><path d="M0.5 2L6 6.5 11.5 2" fill="none" stroke="#fff" stroke-width="1"/></svg>
          harrowgradingllc@maplecove.com
        </li>
        <li>
          <svg viewBox="0 0 12 12"><circle cx="6" cy="6" r="5.3" fill="var(--orange)"/><path d="M1 6h10M6 .7c-2.5 3-2.5 7.6 0 10.6M6 .7c2.5 3 2.5 7.6 0 10.6" fill="none" stroke="#fff" stroke-width="0.8"/></svg>
          www.harrowgrading.com
        </li>
      </ul>
    </div>

    <svg class="front-band" viewBox="0 0 540 12" preserveAspectRatio="none" aria-hidden="true">
      <polygon points="0,6 340,6 346,0 540,0 540,12 0,12" fill="var(--charcoal)"/>
      <polygon points="0,6 340,6 334,12 0,12" fill="var(--orange)"/>
    </svg>
  </section>

  <section class="card card-back" aria-label="Business card back">
    <div class="back-wordmark"><span class="mark-square"></span><span>Harrow Grading LLC</span></div>
  </section>

</div>
</body>
</html>
```